Belmont Ridge Business Card Design Project

We have recently rebranded and would like to design new business cards that incorporate the corporate logo - double sided cards with corporate logo on one side and contact details on the other

Target Market(s)

Sophisticated and high net worth investors and finance industry professionals

Industry/Entity Type

Funds Management

Contact Information for Business Card

The card should prominently feature the company name and logo. Other details will be standard contact details for each staff member - name, address, phone, email, website

Colors
0054AA
0677BA
7BADD7
CADEEF
E8F1F8

Requirements
Must have
• Double-sided design with one side prominently featuring the corporate logo and the other side with all standard contact details

```html
<!DOCTYPE html>
<html lang="en">
<head>
<meta charset="UTF-8">
<title>Belmont Ridge — Business Card</title>
<link href="https://fonts.googleapis.com/css2?family=Arimo:wght@400;700&display=swap" rel="stylesheet">
<style>
  :root {
    --backdrop: #1b1b1b;
    --card-white: #ffffff;
    --navy: #21446f;
    --ink: #1f3f6e;
  }
  * { margin: 0; padding: 0; box-sizing: border-box; }
  html, body {
    width: 1075px;
    height: 1200px;
    overflow: hidden;
    background: var(--backdrop);
    font-family: "Arimo", Arial, sans-serif;
  }
  .card {
    position: absolute;
    left: 205px;
    width: 663px;
    height: 395px;
    overflow: hidden;
  }
  .card-front {
    top: 187px;
    background: var(--card-white);
    color: var(--ink);
  }
  .card-back {
    top: 637px;
    background: var(--navy);
  }
  .corner-disc {
    position: absolute;
    right: -250px;
    bottom: -250px;
    width: 560px;
    height: 560px;
    border-radius: 50%;
    background: var(--navy);
  }
  .person {
    position: absolute;
    left: 37px;
    top: 56px;
  }
  .person-name {
    font-size: 24px;
    font-weight: 700;
    letter-spacing: 0.2px;
    line-height: 1.1;
  }
  .person-role {
    font-size: 17.5px;
    line-height: 1.3;
  }
  .address {
    position: absolute;
    left: 37px;
    top: 146px;
    font-size: 17.5px;
    line-height: 23.4px;
    font-style: normal;
  }
  .contacts {
    position: absolute;
    left: 37px;
    top: 278px;
    list-style: none;
    font-size: 17.5px;
    line-height: 23.4px;
  }
  .contacts li {
    display: flex;
    align-items: center;
    gap: 5px;
  }
  .contacts svg {
    width: 17px;
    height: 17px;
    fill: var(--ink);
    flex-shrink: 0;
  }
  .brand-lockup {
    position: absolute;
    left: 0;
    right: 0;
    top: 222px;
    display: flex;
    align-items: center;
    justify-content: center;
    gap: 18px;
  }
  .brand-square {
    width: 34px;
    height: 34px;
    background: var(--card-white);
  }
  .brand-name {
    color: var(--card-white);
    font-size: 50px;
    font-weight: 400;
    letter-spacing: 1.5px;
    line-height: 1;
  }
</style>
</head>
<body>
  <section class="card card-front" aria-label="Card front with contact details">
    <div class="corner-disc" aria-hidden="true"></div>
    <div class="person">
      <p class="person-name">DANIEL HARTLEY</p>
      <p class="person-role">Managing Director</p>
    </div>
    <address class="address">
      421, Address line<br>
      goes here<br>
      45452,Country Name
    </address>
    <ul class="contacts">
      <li>
        <svg viewBox="0 0 24 24" aria-hidden="true"><path d="M6.6 10.8a15.1 15.1 0 0 0 6.6 6.6l2.2-2.2c.3-.3.7-.4 1-.2 1.1.4 2.3.6 3.6.6.6 0 1 .4 1 1V20c0 .6-.4 1-1 1C10.6 21 3 13.4 3 4c0-.6.4-1 1-1h3.5c.6 0 1 .4 1 1 0 1.3.2 2.5.6 3.6.1.3 0 .7-.2 1z"/></svg>
        <span>044-123 456 789</span>
      </li>
      <li>
        <svg viewBox="0 0 24 24" aria-hidden="true"><path d="M2 5h20v2l-10 7L2 7z M2 9l10 7 10-7v10H2z"/></svg>
        <span>info@belmontridge.com</span>
      </li>
      <li>
        <svg viewBox="0 0 24 24" aria-hidden="true"><path d="M12 2a10 10 0 1 0 0 20 10 10 0 0 0 0-20zm6.9 6h-2.8a15 15 0 0 0-1.3-3.6A8 8 0 0 1 18.9 8zM12 4c.8 1.2 1.5 2.5 1.9 4h-3.8c.4-1.5 1.1-2.8 1.9-4zM4.3 14a8 8 0 0 1 0-4h3.2a16 16 0 0 0 0 4zm.8 2h2.8c.3 1.3.8 2.5 1.3 3.6A8 8 0 0 1 5.1 16zM7.9 8H5.1a8 8 0 0 1 4.1-3.6C8.7 5.5 8.2 6.7 7.9 8zM12 20c-.8-1.2-1.5-2.5-1.9-4h3.8c-.4 1.5-1.1 2.8-1.9 4zm2.3-6H9.7a14 14 0 0 1 0-4h4.6a14 14 0 0 1 0 4zm.5 5.6c.5-1.1 1-2.3 1.3-3.6h2.8a8 8 0 0 1-4.1 3.6zM16.5 14a16 16 0 0 0 0-4h3.2a8 8 0 0 1 0 4z"/></svg>
        <span>www.belmontridge.com</span>
      </li>
    </ul>
  </section>

  <section class="card card-back" aria-label="Card back with company name">
    <div class="brand-lockup">
      <span class="brand-square" aria-hidden="true"></span>
      <p class="brand-name">BELMONT RIDGE</p>
    </div>
  </section>
</body>
</html>
```